Consulting company business cards

We have a base design, but would be willing to update. We have a new logo/"tag" that needs to be added. Current business card design is attached for reference into our "style."

Industry/Entity Type

Business

Contact Information for Business Card

Should contain name and title, office number, mobile number if appropriate, e-mail, website, physical address, and company logo.

Font styles to use
Other font styles liked:
• See current card design on KorvandBCard

Colors
0455a3
85acd3
aaaaaa

Requirements
Must have
• Our colors are navy blue, gray, and a lighter blue
Nice to have
• Design that I can easily drop in new names/titles as we hire employees.

```html
<!DOCTYPE html>
<html lang="en">
<head>
<meta charset="utf-8">
<title>Torvale Business Cards</title>
<link href="https://fonts.googleapis.com/css2?family=Open+Sans:wght@400;600;700&display=swap" rel="stylesheet">
<style>
  :root {
    --navy: #06314f;
    --light-blue: #7aa8cc;
    --gray: #aaaaaa;
    --white: #ffffff;
    --backdrop: #ecebe8;
  }
  * { box-sizing: border-box; margin: 0; padding: 0; }
  html, body { width: 1200px; height: 900px; overflow: hidden; }
  body {
    background: var(--backdrop);
    font-family: "Open Sans", Arial, sans-serif;
    position: relative;
  }
  .card {
    position: absolute;
    width: 525px;
    height: 300px;
    border-radius: 3px;
    box-shadow: 0 8px 22px rgba(0,0,0,0.18);
    overflow: hidden;
  }
  .card-front { left: 70px; top: 150px; background: var(--white); }
  .card-back { left: 605px; top: 450px; background: var(--navy); color: var(--white); }

  .brand { display: flex; align-items: center; gap: 10px; }
  .brand-name { font-weight: 700; letter-spacing: 2px; line-height: 1; }
  .brand-dot { border-radius: 50%; flex: none; }
  .tagline { font-weight: 400; letter-spacing: 2.2px; text-transform: uppercase; }

  .card-front .brand { position: absolute; left: 118px; top: 86px; }
  .card-front .brand-name { font-size: 58px; color: var(--navy); }
  .card-front .brand-dot { width: 54px; height: 54px; background: var(--light-blue); }
  .card-front .tagline { position: absolute; left: 150px; top: 154px; font-size: 13px; color: var(--navy); }
  .card-front .website { position: absolute; left: 0; right: 0; top: 222px; text-align: center; font-size: 13px; color: var(--navy); font-weight: 600; }

  .card-back .brand { position: absolute; right: 30px; top: 28px; }
  .card-back .brand-name { font-size: 40px; color: var(--white); }
  .card-back .brand-dot { width: 36px; height: 36px; background: var(--white); }
  .card-back .tagline { position: absolute; right: 30px; top: 78px; font-size: 9.5px; color: var(--white); }
  .rule { position: absolute; height: 3px; background: var(--gray); }
  .rule-top { left: 240px; right: 0; top: 104px; }
  .rule-bottom { left: 0; right: 0; top: 196px; }

  .person { position: absolute; left: 32px; top: 140px; }
  .person-name { font-size: 17px; font-weight: 700; }
  .person-title { font-size: 14px; }

  .contact { position: absolute; right: 28px; top: 118px; text-align: right; font-size: 11.5px; line-height: 1.55; }
  .contact-line { display: flex; justify-content: flex-end; align-items: center; gap: 5px; }
  .contact-line svg { width: 9px; height: 9px; }
  .email { margin-top: 10px; }
  .address { position: absolute; right: 28px; top: 214px; font-size: 13px; }
</style>
</head>
<body>
  <section class="card card-front" aria-label="Business card front">
    <div class="brand">
      <span class="brand-name">TORVALE</span>
      <span class="brand-dot"></span>
    </div>
    <p class="tagline">A Cloud Consulting Company</p>
    <p class="website">www.torvaletech.com</p>
  </section>

  <section class="card card-back" aria-label="Business card back">
    <div class="brand">
      <span class="brand-name">TORVALE</span>
      <span class="brand-dot"></span>
    </div>
    <p class="tagline">A Cloud Consulting Company</p>
    <div class="rule rule-top"></div>

    <div class="person">
      <p class="person-name">Dana Korvand</p>
      <p class="person-title">Managing Director</p>
    </div>

    <div class="contact">
      <p class="contact-line">555.014.2910
        <svg viewBox="0 0 10 10" aria-hidden="true"><path d="M1 3 Q5 0 9 3 L8 4.5 L6.5 3.8 L6.5 3 Q5 2.5 3.5 3 L3.5 3.8 L2 4.5 Z M2.5 5 H7.5 L8.5 9 H1.5 Z" fill="currentColor"/></svg>
      </p>
      <p class="contact-line">555.014.2971
        <svg viewBox="0 0 10 10" aria-hidden="true"><rect x="2.5" y="0.5" width="5" height="9" rx="1" fill="currentColor"/><rect x="3.4" y="1.6" width="3.2" height="5.5" fill="#06314f"/></svg>
      </p>
      <p class="contact-line">www.torvaletech.com
        <svg viewBox="0 0 10 10" aria-hidden="true"><rect x="0.5" y="2" width="9" height="6.5" fill="currentColor"/><path d="M0.5 2 L5 5.5 L9.5 2" stroke="#06314f" stroke-width="0.9" fill="none"/></svg>
      </p>
      <p class="email">dkorvand@torvaletech.com</p>
    </div>

    <div class="rule rule-bottom"></div>
    <p class="address">1180 N Birch St fairview ohio 45011</p>
  </section>
</body>
</html>
```